BOLD & MINIMALIST DESIGN NEEDED

We want a very bold but minimalistic business card design that is impactful and utilizes both sides of the business card. Our current logo is included for your use.

We want bold fonts and good use of negative space. We don't want the logo to overpower the design.

Target Market(s)

Professionals who are building new commercial buildings.

Industry/Entity Type

Construction

Contact Information for Business Card

Name, Title, email, office phone, cell phone, website

Font styles to use
Serif
Sans Serif

Requirements
Must have
• Bold design!

```html
<!DOCTYPE html>
<html lang="en">
<head>
<meta charset="utf-8">
<title>Ridgeview Design + Build — Business Card</title>
<link rel="stylesheet" href="https://fonts.googleapis.com/css2?family=Montserrat:wght@400;500;700;900&display=swap">
<style>
  :root {
    --stage: #2b2b2d;
    --card: #ffffff;
    --ink: #111111;
    --text: #222222;
    --green: #7dc242;
    --muted: #3a3a3a;
  }
  * { box-sizing: border-box; margin: 0; padding: 0; }
  html, body { width: 1200px; height: 874px; overflow: hidden; }
  body {
    background: var(--stage);
    font-family: "Montserrat", Arial, sans-serif;
    position: relative;
  }
  .card {
    position: absolute;
    width: 640px;
    height: 366px;
    background: var(--card);
    border-radius: 22px;
    overflow: hidden;
    box-shadow: 0 10px 30px rgba(0,0,0,.45);
  }
  .card--front { left: 360px; top: 42px; }
  .card--back { left: 200px; top: 466px; }

  .wordmark {
    position: absolute;
    display: flex;
    align-items: center;
    gap: 14px;
    color: var(--ink);
    font-weight: 900;
    text-transform: uppercase;
    letter-spacing: 1px;
    line-height: 1;
  }
  .wordmark__square { background: var(--green); flex: none; }
  .wordmark__text { display: flex; flex-direction: column; }
  .wordmark__sub { font-size: .36em; letter-spacing: .35em; margin-top: .3em; }

  .card--front .wordmark { left: 0; right: 0; top: 0; bottom: 0; justify-content: center; font-size: 62px; }
  .card--front .wordmark__square { width: 58px; height: 58px; }

  .card--back .wordmark { left: 34px; top: 112px; font-size: 34px; gap: 10px; }
  .card--back .wordmark__square { width: 32px; height: 32px; }

  .divider {
    position: absolute;
    left: 372px; top: 36px;
    width: 2px; height: 212px;
    background: var(--green);
  }
  .contact {
    position: absolute;
    left: 392px; top: 30px;
    color: var(--text);
  }
  .contact__name { color: var(--green); font-weight: 700; font-size: 26px; letter-spacing: .5px; text-transform: uppercase; }
  .contact__title { font-size: 15px; font-weight: 500; margin: 4px 0 14px; text-transform: uppercase; }
  .contact__address { font-size: 16px; line-height: 1.35; margin-bottom: 12px; }
  .contact__list { list-style: none; font-size: 16px; line-height: 1.6; }
  .contact__list li { display: flex; align-items: center; gap: 8px; }
  .contact__list svg { width: 14px; height: 14px; fill: var(--green); flex: none; }

  .swoosh { position: absolute; left: 0; bottom: 0; width: 640px; height: 150px; }
</style>
</head>
<body>

<section class="card card--front" aria-label="Card front">
  <div class="wordmark">
    <span class="wordmark__square"></span>
    <span class="wordmark__text">Ridgeview<span class="wordmark__sub">Design + Build</span></span>
  </div>
</section>

<section class="card card--back" aria-label="Card back">
  <div class="wordmark">
    <span class="wordmark__square"></span>
    <span class="wordmark__text">Ridgeview<span class="wordmark__sub">Design + Build</span></span>
  </div>

  <div class="divider"></div>

  <div class="contact">
    <p class="contact__name">Daniel Marsh</p>
    <p class="contact__title">Owner-CEO</p>
    <p class="contact__address">Your address, City<br>State, Zip 1234</p>
    <ul class="contact__list">
      <li><svg viewBox="0 0 16 16"><path d="M3 1h3l1.5 4-2 1.2a9 9 0 0 0 4.3 4.3L11 8.5l4 1.5v3a2 2 0 0 1-2 2A13 13 0 0 1 1 3a2 2 0 0 1 2-2z"/></svg>123 456 789</li>
      <li><svg viewBox="0 0 16 16"><path d="M4 0h8a1 1 0 0 1 1 1v14a1 1 0 0 1-1 1H4a1 1 0 0 1-1-1V1a1 1 0 0 1 1-1zm1 2v10h6V2zm3 11a1 1 0 1 0 0 2 1 1 0 0 0 0-2z"/></svg>123 456 789</li>
      <li><svg viewBox="0 0 16 16"><path d="M0 3h16v10H0zm1.5 1.2L8 9l6.5-4.8V4h-13z"/></svg>info@ridgeviewbuild.com</li>
      <li><svg viewBox="0 0 16 16"><circle cx="8" cy="8" r="7"/></svg>www.ridgeviewbuild.com</li>
    </ul>
  </div>

  <svg class="swoosh" viewBox="0 0 640 150" preserveAspectRatio="none" aria-hidden="true">
    <path d="M0 10 C 120 70, 300 60, 440 90 C 540 112, 600 120, 640 118 L640 150 L0 150 Z" fill="#111111"/>
    <path d="M0 26 C 140 84, 320 70, 460 104 C 560 126, 610 112, 640 100 L640 150 L0 150 Z" fill="#7dc242"/>
  </svg>
</section>

</body>
</html>
```